Webdesign für HALDEN STAHLWERK
Zielgruppe
Valkorin ist Ihr leistungsstarker und zuverlässiger Partner im Bereich Metallverarbeitung. Seit unserer Firmengründung im Jahr 2001 ist unser inhabergeführtes Unternehmen in Gornau bei Chemnitz kontinuierlich gewachsen und beschäftigt derzeit 20 engagierte und qualifizierte Mitarbeiter.
Mit der Einweihung unserer neuen Fertigungshalle 2010 haben wir unsere Produktionsfläche auf 1.400 m2 vergrößert und können Ihnen nun einen noch umfassenderen Service anbieten.
Von der CNC-gesteuerten Teilefertigung bis zu modernsten Schweiß-, Schneid-, und Bearbeitungsanlagen – für die Realisierung Ihrer individuellen Wünsche steht uns ein innovativer Maschinenpark zur Verfügung. Wir fertigen zuverlässig und termingerecht nach Ihren Plänen oder übernehmen bei Bedarf auch die gesamte Abwicklung Ihres Projektes – alles made in germany!
Das Unternehmen spricht ausschließlich B2B Kunden an.
Die Hauptleistungsbereiche sind:
- Stahl- und Palettenbau
- Blechbearbeitung
- Edelstahlbearbeitung
- Mechanische Fertigung
Aufgabenstellung
- Mitlaufende Kontaktleiste
- Integration der Social Media Kanäle
- Sehr modernes Auftreten
- Industrielles Design
- Verlinkung zum Partnerunternehmen https://www.valkorin-beispiel.de/ias/index.html

```html
<!DOCTYPE html>
<html lang="de">
<head>
<meta charset="utf-8">
<title>Valkorin – Metallverarbeitung</title>
<link href="https://fonts.googleapis.com/css2?family=Montserrat:wght@400;500;600;700;800&display=swap" rel="stylesheet">
<style>
:root{
  --nav:#1f222b;
  --page:#23252f;
  --footer:#1d1f27;
  --blue:#004b9b;
  --accent:#f0a500;
  --white:#ffffff;
  --card:#f1f1f1;
  --ink:#2b2d33;
  --grey:#7a7d85;
  --rule:#3a3d47;
}
*{margin:0;padding:0;box-sizing:border-box}
html,body{width:1200px;height:3250px;overflow:hidden}
body{background:var(--page);font-family:"Montserrat",sans-serif;color:var(--white);position:relative;letter-spacing:.04em}
.abs{position:absolute}
.brand{font-weight:800;font-size:30px;letter-spacing:0;color:var(--white);display:flex;align-items:center;gap:8px}
.brand .dot{width:10px;height:10px;background:var(--blue)}
/* nav */
.site-nav{top:0;left:0;width:1200px;height:75px;background:var(--nav)}
.site-nav .brand{position:absolute;left:64px;top:22px}
.menu{position:absolute;left:550px;top:29px;display:flex;gap:36px;font-size:14px;font-weight:500}
.menu span.drop::after{content:"";display:inline-block;width:5px;height:5px;border-right:1.5px solid var(--white);border-bottom:1.5px solid var(--white);transform:rotate(45deg);margin-left:7px;position:relative;top:-3px}
.btn-contact{position:absolute;left:1012px;top:21px;width:122px;height:33px;border:1px solid var(--white);font-size:12px;font-weight:600;display:flex;align-items:center;justify-content:center}
/* hero */
.hero{top:75px;left:0;width:1200px;height:544px;background:radial-gradient(ellipse at 30% 95%,#b8661a 0%,#5a3614 22%,transparent 50%),linear-gradient(100deg,#1a1d26 0%,#2a3346 45%,#1c2434 70%,#141820 100%)}
.hero h1{position:absolute;left:64px;top:152px;font-size:33px;font-weight:400;letter-spacing:.05em}
.hero p{position:absolute;left:64px;top:205px;width:350px;font-size:15.5px;line-height:26.5px;letter-spacing:.01em}
.btn-outline{position:absolute;border:1px solid var(--accent);color:var(--accent);font-size:12px;font-weight:700;letter-spacing:.12em;display:flex;align-items:center;justify-content:center}
/* features */
.features{top:619px;left:0;width:1200px;height:407px;background:var(--blue)}
.feature{position:absolute;top:110px;width:280px;text-align:center}
.feature svg{display:block;margin:0 auto}
.feature h3{margin-top:30px;font-size:16px;font-weight:500;letter-spacing:.06em}
.feature p{margin-top:12px;font-size:14px;line-height:24.5px;letter-spacing:.03em}
.more{margin-top:36px;color:var(--accent);font-size:12px;font-weight:700;letter-spacing:.12em}
/* about */
.about-photo{left:64px;top:1113px;width:520px;height:454px;background:radial-gradient(circle at 28% 55%,#fff6e0 0%,#f2a640 12%,#7a4a2a 35%,#3a4a78 65%,#2a3558 100%)}
.about h2{position:absolute;left:705px;top:1114px;font-size:30px;font-weight:400;letter-spacing:.05em}
.about p{position:absolute;left:705px;top:1165px;width:430px;font-size:16px;line-height:24.4px}
.about ul{position:absolute;left:705px;top:1349px;list-style:none;font-size:14px}
.about li{height:41px;display:flex;align-items:center;gap:14px}
.about li::before{content:"⟶";color:#8a8d95;font-size:14px}
/* section heads */
.sec-head{left:0;width:1200px;text-align:center}
.sec-head h2{font-size:30px;font-weight:400;letter-spacing:.06em}
.sec-head p{margin-top:22px;font-size:16px}
/* team */
.member{position:absolute;top:1960px;width:338px;height:171px;background:var(--card);color:var(--ink)}
.member .photo{position:absolute;left:13px;top:14px;width:141px;height:143px}
.member .info{position:absolute;left:178px;top:52px}
.member .name{font-size:15.5px;letter-spacing:.02em}
.member .role{margin-top:6px;font-size:11px;color:var(--grey);text-transform:uppercase}
.member .social{margin-top:12px;display:flex;gap:15px}
.member .social i{width:8px;height:8px;border-radius:50%;background:#3a6fb0;display:block}
.member .bar{position:absolute;right:4px;top:47px;width:3px;height:79px;background:#d4d4d4}
/* news */
.news{position:absolute;top:2514px;width:337px;height:265px;text-align:center;font-weight:700}
.news .date{margin-top:32px;font-size:12px;font-weight:500}
.news h4{margin-top:56px;font-size:16px;line-height:26px;letter-spacing:.06em}
.news h4 span{display:block;font-size:15.5px}
/* footer */
.site-footer{top:2890px;left:0;width:1200px;height:360px;background:var(--footer)}
.site-footer .brand{position:absolute;left:64px;top:63px}
.f-about{position:absolute;left:64px;top:102px;width:420px;font-size:13.5px;line-height:28px}
.f-col{position:absolute;top:62px;font-size:14px}
.f-col h5{font-size:15.5px;font-weight:500;margin-bottom:20px}
.f-col li{list-style:none;height:28.5px;font-size:14px}
.f-col li::before{content:"›";font-weight:700;margin-right:14px}
.f-contact p{font-size:14px;line-height:24.5px;letter-spacing:.03em}
.f-icons{display:flex;gap:12px;margin-top:8px}
.f-icons i{width:13px;height:13px;border-radius:2px;background:var(--white);display:block}
.f-rule{position:absolute;left:64px;top:302px;width:1072px;height:1px;background:var(--rule)}
.copy{position:absolute;left:0;width:1200px;top:322px;text-align:center;font-size:14px}
</style>
</head>
<body>

<header class="site-nav abs">
  <div class="brand">VALKORIN<span class="dot"></span></div>
  <nav class="menu"><span>Home</span><span class="drop">Produkte</span><span>Fertigung</span><span>Qualifikation</span></nav>
  <div class="btn-contact">Kontakt</div>
</header>

<section class="hero abs" role="img" aria-label="Metallarbeiter mit Schutzausrüstung schleift Stahl, Funkenflug in dunkler Werkhalle">
  <h1>Lorem Ipsum dolore</h1>
  <p>Lorem ipsum dolor sit amet, consetetur sadipscing elitr, sed diam nonumy eirmod tempor invidunt ut labore et dolore magna aliquyam erat, sed diam voluptua.</p>
  <div class="btn-outline" style="left:64px;top:338px;width:183px;height:41px">JETZT ENTDECKEN</div>
</section>

<section class="features abs">
  <div class="feature" style="left:96px">
    <svg width="28" height="30" viewBox="0 0 28 30" fill="none" stroke="#fff" stroke-width="2"><path d="M4 2h20M4 28h20M6 2c0 8 16 8 16 13S6 20 6 28M22 2c0 8-16 8-16 13s16 5 16 13"/></svg>
    <h3>PRODUKTE</h3>
    <p>Lorem ipsum dolor sit amet, consetetur sadipscing elitr, sed diam nonumy eirmod</p>
    <div class="more">MEHR ERFAHREN &nbsp;→</div>
  </div>
  <div class="feature" style="left:462px">
    <svg width="32" height="30" viewBox="0 0 32 30" fill="none" stroke="#fff" stroke-width="1.6"><path d="M9 2h14l8 13-8 13H9L1 15z"/><path d="M9 2l14 26M23 2L9 28M1 15h30"/></svg>
    <h3>FERTIGUNG</h3>
    <p>Lorem ipsum dolor sit amet, consetetur sadipscing elitr, sed diam nonumy eirmod</p>
    <div class="more">MEHR ERFAHREN &nbsp;→</div>
  </div>
  <div class="feature" style="left:827px">
    <svg width="30" height="30" viewBox="0 0 30 30" fill="none" stroke="#fff" stroke-width="2"><path d="M3 28V3M3 4c8-4 14 5 24 1v14c-10 4-16-5-24-1"/></svg>
    <h3>QUALIFIKATION</h3>
    <p>Lorem ipsum dolor sit amet, consetetur sadipscing elitr, sed diam nonumy eirmod</p>
    <div class="more">MEHR ERFAHREN &nbsp;→</div>
  </div>
</section>

<div class="about-photo abs" role="img" aria-label="Nahaufnahme Trennschleifer an Metall mit hellem Funkenregen"></div>
<section class="about">
  <h2>Was wir machen!</h2>
  <p>Lorem ipsum dolor sit amet, consetetur sadipscing elitr, sed diam nonumy eirmod tempor invidunt ut labore et dolore magna aliquyam erat, sed diam voluptua. At vero eos et accusam et justo duo dolores et ea rebum. Stet clita kasd gubergren, no sea takimata sanctus est Lorem ipsum dolor sit amet.</p>
  <ul><li>Lorem No. 1</li><li>Lorem No. 2</li><li>Lorem No. 3</li></ul>
  <div class="btn-outline" style="left:703px;top:1505px;width:183px;height:42px">JETZT ENTDECKEN</div>
</section>

<div class="sec-head abs" style="top:1808px"><h2>Unser Team</h2><p>Lorem ipsum dolor sit amet, consetetur sadipscing</p></div>

<div class="member" style="left:66px">
  <div class="photo" role="img" aria-label="Porträtfoto Geschäftsführer" style="background:linear-gradient(135deg,#b8bcc4,#4a4e58)"></div>
  <div class="info"><div class="name">Max Mustermann</div><div class="role">CEO</div><div class="social"><i></i><i></i><i></i></div></div>
  <div class="bar"></div>
</div>
<div class="member" style="left:432px">
  <div class="photo" role="img" aria-label="Porträtfoto Abteilungsleiter" style="background:linear-gradient(135deg,#3d4d60,#6a7f96)"></div>
  <div class="info"><div class="name">Max Mustermann</div><div class="role">Leiter XY</div><div class="social"><i></i><i></i><i></i></div></div>
  <div class="bar" style="background:var(--nav)"></div>
</div>
<div class="member" style="left:798px">
  <div class="photo" role="img" aria-label="Porträtfoto Mitarbeiterin Buchhaltung" style="background:linear-gradient(135deg,#e4e2e0,#b89a80)"></div>
  <div class="info"><div class="name">SUE Mustermann</div><div class="role">Buchhaltung</div><div class="social"><i></i><i></i><i></i></div></div>
  <div class="bar"></div>
</div>

<div class="sec-head abs" style="top:2355px"><h2>NEUIGKEITEN</h2><p>Lorem ipsum dolor sit amet, consetetur sadipscing</p></div>

<article class="news" style="left:66px;background:linear-gradient(160deg,#5a6478,#8a7a6a 55%,#3a4456)" role="img" aria-label="Auszubildende mit Schutzhelm in Produktionshalle">
  <div class="date">APR 09</div><h4>AZUBIS FÜR DIE INDUSTRIE<span>Unser Schnuppertag</span></h4>
</article>
<article class="news" style="left:432px;background:linear-gradient(160deg,#4a5a74,#6a7486 50%,#2e3a50)" role="img" aria-label="Zwei Mitarbeiter gehen durch eine Lagerhalle">
  <div class="date">APR 09</div><h4>TAG DER OFFENEN TÜR<span>Lernen Sie uns kennen</span></h4>
</article>
<article class="news" style="left:798px;background:linear-gradient(160deg,#2c3440,#5a6676 50%,#222a36)" role="img" aria-label="Gestapelte Vierkant-Stahlrohre">
  <div class="date">APR 09</div><h4>HAUSMESSE 2023<span>Fachmesse für Fachleute</span></h4>
</article>

<footer class="site-footer abs">
  <div class="brand">VALKORIN<span class="dot"></span></div>
  <p class="f-about">Lorem ipsum dolor sit amet, consetetur sadipscing elitr, sed diam nonumy eirmod tempor invidunt ut labore et dolore magna aliquyam erat, sed diam voluptua.</p>
  <div class="f-col" style="left:522px;top:58px"><h5>Nützliche Links</h5><ul><li>Blog</li><li>FAQ</li><li>Karriere</li><li>Über uns</li><li>Zertifizierungen</li></ul></div>
  <div class="f-col" style="left:704px"><h5>Rechtliches</h5><ul><li>AGB</li><li>Datenschutz</li><li>Impressum</li><li>Kontakt</li></ul></div>
  <div class="f-col f-contact" style="left:888px"><h5>Kontaktieren Sie uns</h5>
    <p style="font-weight:700">VALKORIN</p>
    <p>Halden Stahlwerk</p>
    <p>Lindenweg 12 | 08527 Erlenbrück</p>
    <p>E-Mail: info@valkorin-beispiel.de</p>
    <div class="f-icons"><i></i><i></i><i></i><i></i><i></i></div>
  </div>
  <div class="f-rule"></div>
  <div class="copy">© 2023 VALKORIN, Alle Rechte vorbehalten.</div>
</footer>

</body>
</html>
```